verdant terraces simple classy business card design

my name is colin barrow and I run a gardening business aimed at high class verdant terraces. the business name is verdant terraces and our logo was designed on pixel harbour .My clientel are anything from residential homes to businesses. I take pride in my work and know that I offer a service like no other in my area.
The business card will be used to represent my business and I want it to be not only rememberable, but simplistic and modern. Eye catching too. Of course I would like it relatable to gardening and appealing to the correct clientel - those being garden enthusiasts, prestigious homes and businesses that are after top of the line gardening services like no other on the market.
I am not a typical lawn mowing business so I don't want a typical card design that represents that. The gardens I work with are generally million dollar properties with owners who are very garden proud looking for upkeep and guidance from me along with sometimes whole new garden designs. I want the business cards to show to my clients that I take pride, as they do, in their garden. And I want them to know from my card that I am a professional, qualified horticulturist offering them a top of the line service for life. I want them to refer my business on. I want them to look at my business card and see class and professionalism in a modern unique bold way.
The card should be simple with the possibility of the logo on the front being embossed/debossed and my details on the back the card should have a organic garden feel it's very important to me that it is absolutely perfect
I am also very open to ideas and suggestions so look forward to seeing the designs. the business logo has been supplied with this project and I want the card to be double sided

Contact info is
Colin Barrow - Managing Director / Horticulturist
Phone : 0481 526 704
Email: colinbarrow@verdantterraces.example.au

Target Market(s)

high class gardens residential and commercial

Industry/Entity Type

Gardener

Contact Information for Business Card

Contact info is
Phone : 0481 526 704

PLEASE MAKE CARD DOUBLE SIDED

Requirements
Must have
• organic simple classy modern feel
• must flow with the current logo that has been supplied with this project
• Double sided
• Must explain in a simple way that I deal with high end gardens and I'm a qualified horticulturist
Nice to have
• embossed debossed logo
Should not have
• shouldn't be to busy or cheap looking

```html
<!DOCTYPE html>
<html lang="en">
<head>
<meta charset="utf-8">
<title>Verdant Terraces – Business Card</title>
<link href="https://fonts.googleapis.com/css2?family=Arimo:wght@400;700&display=swap" rel="stylesheet">
<style>
  :root {
    --backdrop: #8d8d8d;
    --paper: #eeeeec;
    --leaf-green: #538945;
    --leaf-green-soft: #6f9f62;
    --ink-light: #ffffff;
  }
  * { margin: 0; padding: 0; box-sizing: border-box; }
  html, body {
    width: 1105px;
    height: 1200px;
    overflow: hidden;
    background: var(--backdrop);
    font-family: "Arimo", Arial, sans-serif;
  }
  .card {
    position: absolute;
    left: 182px;
    width: 746px;
    height: 426px;
    overflow: hidden;
  }
  .card--details { top: 120px; background: var(--leaf-green); }
  .card--brand { top: 637px; background: var(--leaf-green); }

  .details-header {
    position: absolute;
    left: 0; top: 0;
    width: 100%;
    height: 213px;
    background: var(--paper);
  }
  .brand-mark {
    position: absolute;
    display: flex;
    flex-direction: column;
    align-items: center;
    text-align: center;
  }
  .brand-mark__dot {
    width: 84px;
    height: 84px;
    border-radius: 50%;
    margin-bottom: 18px;
  }
  .brand-mark__name {
    font-weight: 400;
    font-size: 34px;
    letter-spacing: 3px;
    text-transform: uppercase;
    line-height: 1.15;
  }
  .details-header .brand-mark { left: 36px; top: 22px; width: 322px; }
  .details-header .brand-mark__dot { background: var(--leaf-green); }
  .details-header .brand-mark__name { color: var(--leaf-green); }

  .contact {
    position: absolute;
    left: 36px;
    top: 243px;
    color: var(--ink-light);
  }
  .contact__name { font-size: 24px; font-weight: 700; line-height: 1; }
  .contact__role { font-size: 19px; font-weight: 400; margin-top: 10px; }
  .contact__list { list-style: none; margin-top: 22px; font-size: 16px; line-height: 29px; }

  .decor-canopy {
    position: absolute;
    left: 502px;
    top: 212px;
    width: 166px;
    height: 166px;
    border-radius: 50%;
    background: var(--leaf-green-soft);
  }

  .card--brand .brand-mark { left: 0; top: 112px; width: 100%; }
  .card--brand .brand-mark__dot { background: var(--ink-light); }
  .card--brand .brand-mark__name { color: var(--ink-light); font-size: 40px; }
  .brand-web {
    position: absolute;
    left: 0; top: 356px;
    width: 100%;
    text-align: center;
    color: var(--ink-light);
    font-size: 18px;
    letter-spacing: 3px;
  }
</style>
</head>
<body>
  <section class="card card--details">
    <div class="details-header">
      <div class="brand-mark">
        <span class="brand-mark__dot"></span>
        <span class="brand-mark__name">Verdant Terraces</span>
      </div>
    </div>
    <div class="contact">
      <p class="contact__name">Colin Barrow</p>
      <p class="contact__role">Managing Director / Horticulturist</p>
      <ul class="contact__list">
        <li>P : 0481 526 704</li>
        <li>E : colinbarrow@verdantterraces.example.au</li>
        <li>W : verdantterraces.example.au</li>
      </ul>
    </div>
    <div class="decor-canopy"></div>
  </section>

  <section class="card card--brand">
    <div class="brand-mark">
      <span class="brand-mark__dot"></span>
      <span class="brand-mark__name">Verdant Terraces</span>
    </div>
    <p class="brand-web">www.verdantterraces.example.au</p>
  </section>
</body>
</html>
```